A 'new law' boutique Australian law firm that provides specialist employment law and people managem

We value helping clients create results with respect workplaces. What differentiates us is we provide actionable training in understanding and dealing with people and ensure legal compliance fits with this approach. We would like a fresh approach to our training overview documents that we currently use in our current law firm (6 attached). Please use pictures, symbols etc consistent with our non-traditional law approach that captures the approach of each training session.. Attached is the logo and draft letterhead for Birchwell Legal which will launch soon.

Target Market(s)

HR Managers and in-house lawyers (non employment specialists) in mid-large Australian companies that are progressive with a relationship based approach to managing employee behaviours and disputes.

Industry/Entity Type

Human Resource

Font styles to use
Sans Serif

Colors
3176b5
33a6d7

Requirements
Must have
• 1 or 2 page PDF for each of the 6 documents that the wording supplied goes into your design which will be pretty similar as we want consistency with our documents

```html
<!DOCTYPE html>
<html lang="en">
<head>
<meta charset="utf-8">
<title>Co-Operatively Compliant Workplaces – Birchwell Legal</title>
<link rel="stylesheet" href="https://fonts.googleapis.com/css2?family=Merriweather:wght@300;400;700&family=Open+Sans:wght@400;600&display=swap">
<style>
  :root{
    --brand-blue:#3176b5;
    --header-blue:#1f74ba;
    --sky:#33a6d7;
    --panel-strong:#45b8e8;
    --panel-mid:#83cdef;
    --panel-pale:#d9eef9;
    --slab:#2e2d30;
    --title-blue:#5fc2ef;
    --heading-navy:#1f3a57;
    --ink:#2f3135;
    --white:#ffffff;
  }
  *{margin:0;padding:0;box-sizing:border-box}
  html,body{width:848px;height:1200px;overflow:hidden;background:var(--white)}
  body{font-family:"Merriweather",Georgia,serif;color:var(--ink);position:relative}
  .page{position:relative;width:848px;height:1200px;overflow:hidden}

  /* header */
  .header-band{position:absolute;left:0;top:0;width:505px;height:118px}
  .brand{position:absolute;left:34px;top:78px;display:flex;align-items:center;gap:8px;white-space:nowrap}
  .brand-dot{width:12px;height:12px;border-radius:50%;background:var(--brand-blue)}
  .brand-name{font-family:"Merriweather",Georgia,serif;font-weight:700;font-size:20px;line-height:24px;color:var(--brand-blue)}
  .contact{position:absolute;left:305px;top:66px;font-family:"Open Sans",Arial,sans-serif;font-size:12.5px;color:var(--white);line-height:20px}
  .contact li{list-style:none;display:flex;align-items:center;gap:6px}
  .contact svg{width:13px;height:13px}

  /* dark slab */
  .slab{position:absolute;left:0;top:128px;width:505px;height:757px}
  .title{position:absolute;right:392px;top:216px;text-align:right;white-space:nowrap}
  .title-line1{font-weight:400;font-size:35px;color:var(--white);line-height:44px}
  .title-line2{font-weight:400;font-size:34px;color:var(--title-blue);line-height:44px}
  .need-heading{position:absolute;right:392px;top:320px;font-size:20px;color:var(--sky);font-weight:400}
  .need-body{position:absolute;right:392px;top:354px;text-align:right;font-weight:300;font-size:11.6px;line-height:17px;color:var(--white);white-space:nowrap}
  .need-body p{margin-bottom:4px}

  .icon-ring{position:absolute;left:79px;top:810px;width:142px;height:142px;border-radius:50%;background:var(--white)}
  .icon-disc{position:absolute;left:13px;top:13px;width:116px;height:116px;border-radius:50%;border:4px solid #6d6e71;background:var(--title-blue)}

  /* learning outcomes */
  .outcomes{position:absolute;left:60px;top:955px;width:400px}
  .outcomes h2{font-weight:400;font-size:20px;color:var(--brand-blue);margin-bottom:14px}
  .outcomes h3{font-weight:700;font-size:11.6px;margin-bottom:6px}
  .outcomes ol{padding-left:12px;font-weight:300;font-size:11.6px;line-height:17px}
  .outcomes li{margin-bottom:4px}

  /* right column */
  .panel{position:absolute;left:505px;width:343px;clip-path:polygon(0 0,100% 0,100% 100%,38px 100%,0 calc(100% - 48px))}
  .panel.strong{background:var(--panel-strong)}
  .panel.mid{background:var(--panel-mid)}
  .panel.pale{background:var(--panel-pale)}
  .panel-inner{position:absolute;left:40px;right:30px}
  .overview-title{font-size:20px;font-weight:400;color:#1c6aae;margin-bottom:8px}
  .panel h2{font-size:16.5px;font-weight:400;color:var(--heading-navy);line-height:21px;margin-bottom:10px}
  .panel ul{list-style:none;font-weight:300;font-size:11.6px;line-height:17px;color:var(--white)}
  .panel.pale ul{color:var(--ink)}
  .panel li{position:relative;padding-left:8px;margin-bottom:4px}
  .panel li::before{content:"";position:absolute;left:0;top:7px;width:3px;height:3px;border-radius:50%;background:currentColor}
</style>
</head>
<body>
<div class="page">

  <svg class="header-band" viewBox="0 0 505 118" aria-hidden="true">
    <polygon points="172,0 505,0 505,118 240,118" fill="var(--header-blue)"/>
  </svg>
  <div class="brand"><span class="brand-dot"></span><span class="brand-name">Birchwell Legal</span></div>
  <ul class="contact">
    <li><svg viewBox="0 0 14 14"><circle cx="7" cy="7" r="6.5" fill="#fff"/><circle cx="7" cy="7" r="4" fill="none" stroke="#1f74ba" stroke-width="1"/><line x1="3" y1="7" x2="11" y2="7" stroke="#1f74ba"/></svg>www.birchwelllegal.com.au</li>
    <li><svg viewBox="0 0 14 14"><circle cx="7" cy="7" r="6.5" fill="#fff"/><rect x="3.5" y="4.5" width="7" height="5" fill="none" stroke="#1f74ba"/><polyline points="3.5,4.5 7,7.5 10.5,4.5" fill="none" stroke="#1f74ba"/></svg>info@birchwelllegal.com.au</li>
  </ul>

  <svg class="slab" viewBox="0 0 505 757" aria-hidden="true">
    <polygon points="0,0 466,0 505,48 505,757 42,757 0,710" fill="var(--slab)"/>
  </svg>

  <div class="title">
    <div class="title-line1">Co-Operatively</div>
    <div class="title-line2">Compliant Workplaces</div>
  </div>
  <h2 class="need-heading">Training Need</h2>
  <div class="need-body">
    <p>Unresolved conflict often builds and leads to costly claims that result<br>in the right people leaving, reduced productivity and low morale.</p>
    <p>There have been major advances in laws protecting diversity and a real<br>push towards inclusiveness. This has coincided with rapid changes to<br>the workforce and diversity being desirable. So then, what’s the problem?</p>
    <p>Why do record payouts keep being broken for sexual harassment and<br>discrimination claims?</p>
    <p>Why has there been a social media explosion<br>on bullying and bad behaviour?</p>
    <p>Traditional processes just aren’t working. They are usually:<br>a ) unnecessarily formal;<br>b) focused on being seen to be doing something<br>than actually doing something effective;<br>c) adversarial; and<br>d) responsible for creating outcomes which range<br>from ‘nothing really changes’ to an ‘overkill’.</p>
    <p>When people don’t know what the rules are they are more focused<br>on not getting it wrong rather than getting it right.</p>
    <p>For organisations who are frustrated by an overemphasis on language<br>to avoid causing offence and a fear of legal claims, this training offers a<br>relationship-based approach to compliance. Unlike traditional training, this<br>training focuses on ground rules for practically understanding workplace<br>behaviour laws and guidelines for dealing with inevitable conflict.</p>
    <p>This training will benefit workplaces where<br>there is unresolved team conflict or lack<br>of self-awareness as to the impact<br>of behaviours on others.</p>
  </div>

  <div class="icon-ring">
    <div class="icon-disc" role="img" aria-label="Handshake icon representing cooperation"></div>
  </div>

  <section class="outcomes">
    <h2>Learning Outcomes</h2>
    <h3>Participants will apply the learnings to understand:</h3>
    <ol>
      <li>What diversity and inclusiveness means and why it is a ‘must have’ for success and not simply a ‘must avoid’ for compliance.</li>
      <li>Different perspectives and that building professional relationships is crucial for effective performance and not being ‘proved right’.</li>
      <li>Lawful and effective workplace behaviour in terms of what’s ok, what’s not ok, what’s grey and how to deal with that.</li>
      <li>How to be more comfortable with uncomfortable conversations that need to occur to work cooperatively and achieve results and not avoidance for fear of legal claims.</li>
    </ol>
  </section>

  <section class="panel strong" style="top:0;height:257px">
    <div class="panel-inner" style="top:38px">
      <h1 class="overview-title">Training Overview</h1>
      <h2>Social Safety is Basic Biology</h2>
      <ul>
        <li>What is a socially safe workplace and why it matters</li>
        <li>A WH&amp;S approach to cooperative workplace behaviour</li>
        <li>Diversity: what does it mean and its benefits</li>
        <li>Balancing act: valuing different perspectives and shared values</li>
      </ul>
    </div>
  </section>

  <section class="panel mid" style="top:257px;height:198px">
    <div class="panel-inner" style="top:30px">
      <h2>Building Effective Relationships:<br>Trust and Respect</h2>
      <ul>
        <li>The 4 natural work styles: self-awareness and understanding others</li>
        <li>Don’t avoid the conversation: creating safe spaces to resolve conflict before ‘pinch points’ become a crunch</li>
      </ul>
    </div>
  </section>

  <section class="panel pale" style="top:455px;height:300px">
    <div class="panel-inner" style="top:30px">
      <h2>Ground Rules:<br>Understanding the workplace<br>behaviour legal framework</h2>
      <ul>
        <li>What is and isn’t bullying, discrimination, sexual harassment, adverse action and victimisation</li>
        <li>Appropriate versus inappropriate behaviour</li>
        <li>What is and isn’t reasonable management action</li>
        <li>Unfair dismissal, adverse action, discrimination, bullying and stress claims</li>
        <li>Individual legal liability</li>
      </ul>
    </div>
  </section>

  <section class="panel strong" style="top:755px;height:290px">
    <div class="panel-inner" style="top:21px">
      <h2>Guidelines: How to avoid<br>unlawful behaviour and<br>generally be effective in a<br>diverse workplace</h2>
      <ul>
        <li>Not a ‘one size fits all’: Applying the understanding of natural workstyles to identify and deal with potential bullying, sexual harassment and discrimination</li>
        <li>Understanding your why: identify and challenge your biases</li>
        <li>Risk management: understanding relationships and context</li>
      </ul>
    </div>
  </section>

  <section class="panel mid" style="top:1045px;height:155px;clip-path:none">
    <div class="panel-inner" style="top:28px">
      <h2>Activities</h2>
      <ul>
        <li>Scenarios to identify potential unlawful or inappropriate behaviour and reasonable action to raise and respond</li>
        <li>Questionnaire to demonstrate due diligence</li>
      </ul>
    </div>
  </section>

</div>
</body>
</html>
```